food delivery web site design

Currently we have a smartphone app (ios/android) that is being used by our clients to make orders to about 30 different restaurants.

We would like to extent this and have also a website that is able to mimic the same functionalities:
- register
- show restaurants based on the selected address
- make order to an restaurant
- being able to process orders for other registered users (please read the attached doc for complete info on this)

Take a look at the attached doc for more info.

```html
<!DOCTYPE html>
<html lang="ro">
<head>
<meta charset="utf-8">
<title>Bucătel – La Hanul Vechi – Meniu</title>
<link href="https://fonts.googleapis.com/css2?family=Oswald:wght@300;400;500&family=Open+Sans:ital,wght@0,400;0,600;1,600&display=swap" rel="stylesheet">
<style>
:root{
  --red:#a51a12;
  --red-dark:#7d130d;
  --ink:#2a2322;
  --dark:#231c1b;
  --gold:#f3c419;
  --yellow:#f7d96a;
  --grey:#8a8a8a;
  --light:#e3e3e3;
  --pattern:#f1f1f1;
  --green:#4a9a1e;
  --white:#fff;
}
*{margin:0;padding:0;box-sizing:border-box}
html,body{width:1040px;height:1200px;overflow:hidden;background:var(--white)}
body{position:relative;font-family:'Open Sans',sans-serif;color:var(--ink)}
.abs{position:absolute}
.top-pattern{left:0;top:0;width:1040px;height:43px;background:var(--pattern)}
.topbar{left:0;top:43px;width:1040px;height:47px;background:var(--red);border-top:2px solid var(--red-dark);border-bottom:2px solid var(--red-dark)}
.topbar .rule{position:absolute;top:22px;height:1px;background:rgba(255,255,255,.5)}
.call{left:304px;top:55px;font-family:'Oswald',sans-serif;font-size:20px;color:var(--white);letter-spacing:-.3px;display:flex;align-items:center;gap:6px}
.call .num{color:var(--gold)}
.dots{left:528px;top:67px;width:240px;border-top:2px dotted rgba(255,255,255,.45)}
.auth{top:59px;font-family:'Oswald',sans-serif;font-size:13px;color:var(--white);display:flex;align-items:center;gap:5px}
.brand{left:120px;top:0;width:136px;height:136px}
.brand-name{left:140px;top:54px;width:98px;text-align:center;font-family:'Oswald',sans-serif;font-size:20px;font-weight:500;color:var(--red)}
.cart{left:768px;top:90px;width:152px;height:108px;background:var(--dark);box-shadow:0 2px 6px rgba(0,0,0,.35)}
.cart-head{display:flex;height:29px;align-items:center;font-family:'Oswald',sans-serif;font-size:12px;color:var(--white)}
.cart-head .title{flex:1;padding-left:9px;display:flex;gap:5px;align-items:center}
.cart-head .details{background:var(--yellow);color:var(--ink);height:29px;line-height:29px;padding:0 8px}
.cart-list{list-style:none;padding:4px 0 0 10px;border-top:1px solid #3a3231}
.cart-list li{display:flex;justify-content:space-between;height:24px;align-items:center;font-family:'Oswald',sans-serif;font-weight:300;font-size:10px;color:var(--white);padding-right:8px}
.cart-list b{font-weight:500;font-size:14px;letter-spacing:6px}
.thumb{left:120px;top:198px;width:54px;height:44px;background:linear-gradient(135deg,#8b7866,#3e342e)}
.rest-name{left:184px;top:194px;font-family:'Oswald',sans-serif;font-size:25px;color:var(--red);letter-spacing:-.3px}
.stars{left:184px;top:232px;display:flex;gap:4px;align-items:center}
.stars a{font-size:9px;font-weight:600;color:var(--green);margin-left:6px;text-decoration:underline}
.meta{top:204px;font-family:'Oswald',sans-serif;font-size:16px;color:#3a3333;display:flex;align-items:center;gap:5px}
.menu-word{left:781px;top:182px;font-family:'Oswald',sans-serif;font-size:66px;color:#c9c9c9;letter-spacing:1px}
.divider{left:120px;top:256px;width:800px;height:1px;background:#cfcfcf}
.sidebar{left:120px;top:258px;width:152px;border-left:1px solid var(--light)}
.sidebar h3{height:30px;background:var(--dark);color:var(--white);font-family:'Oswald',sans-serif;font-weight:300;font-size:15px;line-height:30px;padding-left:11px}
.sidebar ul{list-style:none}
.sidebar li{height:33.6px;line-height:33.6px;border-bottom:1px solid var(--light);padding-left:11px;font-family:'Oswald',sans-serif;font-size:14px;color:var(--grey)}
.sidebar li.active{color:var(--red);border-left:3px solid var(--red);padding-left:13px;margin-left:0}
.vline{left:272px;top:258px;width:1px;height:894px;background:var(--light)}
.items{left:273px;top:272px;width:647px;list-style:none}
.item{position:relative;height:65.6px;border-bottom:1px dotted #bdbdbd;padding:8px 0 0 33px}
.item .name{font-size:16px;font-weight:600;color:#2b2b2b;letter-spacing:.2px}
.item .price{font-size:16px;font-weight:600;color:#6b6b6b}
.item .price i{font-size:12px}
.qty{position:absolute;left:384px;top:20px;width:56px;height:26px;border:1px solid #d8d8d8;border-bottom:2px solid #b5b5b5;display:flex;align-items:center;font-size:15px}
.qty b{width:16px;text-align:center;font-weight:600;color:#333}
.qty b:first-child{margin-left:4px}
.qty span{border-left:1px solid #ddd;padding-left:5px;margin-left:2px;color:var(--red);font-size:14px}
.footer{left:0;top:1152px;width:1040px;height:48px;background:#2b2625;color:#e5e5e5;font-size:10.5px}
.footer nav{position:absolute;left:120px;top:16px;display:flex}
.footer nav span{padding:0 8px;border-right:1px solid #666}
.footer nav span:first-child{padding-left:0}
.footer nav span:last-child{border:0}
.footer .copy{position:absolute;right:120px;top:16px}
</style>
</head>
<body>
<div class="abs top-pattern" role="img" aria-label="Fundal decorativ cu desene de alimente"></div>
<header class="abs topbar">
  <div class="rule" style="left:0;width:120px"></div>
  <div class="rule" style="left:256px;width:32px"></div>
  <div class="rule" style="left:922px;width:118px"></div>
</header>
<svg class="abs brand" viewBox="0 0 136 136" aria-hidden="true">
  <path d="M2 0H134V108L114 134H22L2 108Z" fill="#2f2726"/>
  <path d="M8 0H128V104L110 126H26L8 104Z" fill="#231c1b"/>
  <circle cx="68" cy="67" r="48" fill="#fff"/>
  <circle cx="68" cy="67" r="42" fill="#f2f2f2"/>
</svg>
<div class="abs brand-name">Bucătel</div>
<div class="abs call">SUNĂ-NE LA
  <svg width="14" height="16" viewBox="0 0 14 16"><path d="M3 1l3 3-2 2c1 2 3 4 5 5l2-2 3 3-2 3C7 15 0 8 1 3z" fill="#f3c419"/></svg>
  <span class="num">0700 555 123</span></div>
<div class="abs dots"></div>
<div class="abs auth" style="left:784px"><svg width="12" height="11" viewBox="0 0 12 11"><path d="M1 10V6c0-2 2-3 4-3h3V0l4 4-4 4V5H5C3 5 2 7 1 10z" fill="#fff"/></svg>LOGIN</div>
<div class="abs auth" style="left:850px"><svg width="14" height="11" viewBox="0 0 14 11"><circle cx="5" cy="3" r="3" fill="#fff"/><path d="M0 11c0-3 2-5 5-5s5 2 5 5z" fill="#fff"/><path d="M11 1v4M9 3h4" stroke="#fff" stroke-width="1.4"/></svg>SIGN IN</div>

<aside class="abs cart">
  <div class="cart-head"><div class="title"><svg width="13" height="11" viewBox="0 0 13 11"><path d="M0 1h2l2 6h7l2-5H3" stroke="#fff" fill="none" stroke-width="1.2"/><circle cx="5" cy="9.5" r="1" fill="#fff"/><circle cx="10" cy="9.5" r="1" fill="#fff"/></svg>COŞUL MEU</div><div class="details">DETALII</div></div>
  <ul class="cart-list">
    <li>ZACUSCĂ DE VINETE (3)<b>+-</b></li>
    <li>FASOLE BĂTUTĂ (3)<b>+-</b></li>
    <li>"TACI ŞI-NGHITE!" (1)<b>+-</b></li>
  </ul>
</aside>

<div class="abs thumb" role="img" aria-label="Fotografia restaurantului"></div>
<h1 class="abs rest-name">LA HANUL VECHI</h1>
<div class="abs stars">
  <svg width="86" height="13" viewBox="0 0 86 13" aria-label="5 stele">
    <g fill="#e8b70e"><path id="s" d="M6.5 0l1.9 4.3 4.6.4-3.5 3 1.1 4.6-4.1-2.5-4.1 2.5 1.1-4.6L0 4.7l4.6-.4z"/><use href="#s" x="17.5"/><use href="#s" x="35"/><use href="#s" x="52.5"/><use href="#s" x="70"/></g>
  </svg><a>35 DE REVIEW-URI</a></div>
<div class="abs meta" style="left:392px"><svg width="16" height="16" viewBox="0 0 16 16"><path d="M2 2l12 12M4 2l-2 2 4 4" stroke="#a51a12" stroke-width="1.8" fill="none"/></svg>ROMANESC</div>
<div class="abs meta" style="left:509px"><svg width="14" height="17" viewBox="0 0 14 17"><path d="M6 0h2v17H6z" fill="#a51a12"/><path d="M1 3h12l-2 2 2 2H1zM1 9h12v4H1z" fill="#a51a12"/></svg>3KM</div>
<div class="abs meta" style="left:578px"><svg width="18" height="12" viewBox="0 0 18 12"><g fill="#a51a12"><rect y="1" width="11" height="3" rx="1.5"/><rect y="5" width="11" height="3" rx="1.5"/><rect y="9" width="11" height="3" rx="1.5"/><rect x="12" y="5" width="6" height="3" rx="1.5"/><rect x="12" y="9" width="6" height="3" rx="1.5"/></g></svg>&lt; 25RON</div>
<div class="abs meta" style="left:678px"><svg width="16" height="16" viewBox="0 0 16 16"><circle cx="8" cy="8" r="6.5" stroke="#a51a12" stroke-width="1.8" fill="none"/><path d="M8 4v4h3" stroke="#a51a12" stroke-width="1.6" fill="none"/></svg>25MIN</div>
<div class="abs menu-word">MENIU</div>
<div class="abs divider"></div>

<nav class="abs sidebar">
  <h3>CATEGORII</h3>
  <ul>
    <li class="active">GUSTĂRI</li><li>CIORBE</li><li>PEŞTE</li><li>PREGĂTITE ÎN CASĂ</li><li>GRĂTAR</li><li>GARNITURI</li><li>SALATE</li><li>DESERT</li><li>BĂUTURI</li>
  </ul>
</nav>
<div class="abs vline"></div>

<ul class="abs items">
  <li class="item"><div class="name">Zacuscă de vinete</div><div class="price">11.00 RON</div><div class="qty"><b>+</b><b>-</b><span>3</span></div></li>
  <li class="item"><div class="name">Salată de icre de crap</div><div class="price">16.00 RON</div><div class="qty"><b>+</b><b>-</b><span>0</span></div></li>
  <li class="item"><div class="name">Salata de icre de ştiucă</div><div class="price">22.00 RON</div><div class="qty"><b>+</b><b>-</b><span>0</span></div></li>
  <li class="item"><div class="name">Fasole bătută</div><div class="price">11.00 RON</div><div class="qty"><b>+</b><b>-</b><span>3</span></div></li>
  <li class="item"><div class="name">Salată Isaccea</div><div class="price">19.00 RON</div><div class="qty"><b>+</b><b>-</b><span>0</span></div></li>
  <li class="item"><div class="name">Colţunaşi cu mânătărci</div><div class="price">23.00 RON</div><div class="qty"><b>+</b><b>-</b><span>0</span></div></li>
  <li class="item"><div class="name">Jumări Româneşti</div><div class="price">7.00 RON <i>(100gr/por)</i></div><div class="qty"><b>+</b><b>-</b><span>0</span></div></li>
  <li class="item"><div class="name">Tobă Ţărănească</div><div class="price">7.00 RON <i>(100gr/por)</i></div><div class="qty"><b>+</b><b>-</b><span>0</span></div></li>
  <li class="item"><div class="name">Slănină Afumată</div><div class="price">3.00 RON <i>(50gr/por)</i></div><div class="qty"><b>+</b><b>-</b><span>0</span></div></li>
  <li class="item"><div class="name">Şorici</div><div class="price">9.00 RON <i>(50gr/por)</i></div><div class="qty"><b>+</b><b>-</b><span>0</span></div></li>
  <li class="item"><div class="name">Caltaboş</div><div class="price">7.00 RON <i>(100gr/por)</i></div><div class="qty"><b>+</b><b>-</b><span>0</span></div></li>
  <li class="item"><div class="name">Lebăr</div><div class="price">6.00 RON <i>(100gr/por)</i></div><div class="qty"><b>+</b><b>-</b><span>0</span></div></li>
</ul>

<footer class="abs footer" role="contentinfo">
  <nav><span>Contactează-ne</span><span>Despre noi</span><span>Partenerii noştri</span><span>FAQ</span><span>Devino partener</span></nav>
  <div class="copy">Copyright © 2013 bucatel.ro. Toate drepturile rezervate.</div>
</footer>
</body>
</html>
```